I need a sophisticated and powerful book cover design that combines Japanese minimalism with contemporary appeal. The cover should convey personal transformation through the metaphor of a katana (Japanese sword).
Key Design Elements:
A katana, either partially shown or artistically rendered
Subtle Japanese design elements without being stereotypical
Clean, minimalist aesthetic
Professional font selection that bridges Eastern and Western typography
Color scheme: Deep blacks, steel grays, and possibly a touch of red or gold for accent
Mood/Style:
Professional and sophisticated
Blend of traditional Japanese aesthetics with modern design
Should appeal to personal development and business readers
Must convey strength and transformation
Elegant rather than aggressive
Specific Requirements:
Title: "The Lantern Compass"
Subtitle: "Quiet Methods for Growing Inner Steadiness and Calm Endurance"
Author names: Dorvelan Thaske and Meloda Thaske
Cover dimensions: Standard hardcover book size (6" x 9")
Must work well in both physical and digital thumbnail formats
Should be striking and legible when viewed as a small image online
Design Specifics:
Japanese elements such as brushstroke effects, kanji characters, or wave patterns
The design should reflect the book's core message: personal transformation through Japanese wisdom principles, using the katana as a metaphor for growth and development.

```html
<!DOCTYPE html>
<html lang="en">
<head>
<meta charset="utf-8">
<title>The Lantern Compass — Book Cover</title>
<link rel="stylesheet" href="https://fonts.googleapis.com/css2?family=Montserrat:wght@500;800;900&display=swap">
<style>
  :root {
    --backdrop: #000000;
    --paper: #ffffff;
    --sun-red: #ec2227;
    --sun-deep: #c9262a;
    --ink: #111111;
    --steel-light: #f1f3f6;
    --steel-mid: #9aa1ad;
    --hilt-dark: #1c2233;
    --blossom: #f4b8c4;
  }
  * { margin: 0; padding: 0; box-sizing: border-box; }
  html, body {
    width: 1200px; height: 1200px; overflow: hidden;
    background: var(--backdrop);
  }
  .cover {
    position: absolute; left: 240px; top: 60px;
    width: 720px; height: 1080px;
    background: var(--paper);
    overflow: hidden;
    font-family: "Montserrat", sans-serif;
  }
  .sun-brush {
    position: absolute; left: 30px; top: 60px;
    width: 660px; height: 660px;
  }
  .blossom-branch {
    position: absolute; left: 0; top: 0;
    width: 150px; height: 130px;
  }
  .blade {
    position: absolute; left: 300px; top: 14px;
    width: 120px; height: 824px;
  }
  .title {
    position: absolute; left: 0; right: 0; top: 545px;
    text-align: center; line-height: 1;
  }
  .title-small {
    display: block;
    font-weight: 900; font-size: 80px; letter-spacing: 6px;
    color: var(--ink);
    text-shadow: 0 0 4px var(--paper), 0 0 8px var(--paper);
  }
  .title-main {
    display: block;
    font-weight: 800; font-size: 104px; letter-spacing: 2px;
    color: var(--sun-red);
    margin-top: 14px;
  }
  .title-main + .title-main { margin-top: 2px; }
  .subtitle {
    position: absolute; left: 80px; right: 80px; top: 848px;
    text-align: center;
    font-weight: 500; font-size: 25px; line-height: 34px;
    color: var(--ink); letter-spacing: 0.5px;
  }
  .authors {
    position: absolute; left: 0; right: 0; top: 984px;
    text-align: center;
    font-weight: 500; font-size: 34px;
    color: var(--ink);
  }
</style>
</head>
<body>
  <main class="cover">
    <svg class="blossom-branch" role="img" aria-label="Cherry blossom branch in the top corner" viewBox="0 0 150 130">
      <defs>
        <linearGradient id="blossomTone" x1="0" y1="0" x2="1" y2="1">
          <stop offset="0" stop-color="#f7c9d2"/>
          <stop offset="1" stop-color="#ffffff" stop-opacity="0"/>
        </linearGradient>
      </defs>
      <rect width="150" height="130" fill="url(#blossomTone)"/>
    </svg>

    <svg class="sun-brush" role="img" aria-label="Red brushstroke sun circle" viewBox="0 0 660 660">
      <defs>
        <radialGradient id="sunTone" cx="0.5" cy="0.45" r="0.5">
          <stop offset="0" stop-color="#ef1c23"/>
          <stop offset="0.8" stop-color="#ec2a2e"/>
          <stop offset="1" stop-color="#c42d2f"/>
        </radialGradient>
      </defs>
      <circle cx="330" cy="330" r="322" fill="url(#sunTone)"/>
    </svg>

    <svg class="blade" role="img" aria-label="Vertical katana with wrapped hilt and steel blade" viewBox="0 0 120 824">
      <defs>
        <linearGradient id="bladeTone" x1="0" y1="0" x2="0" y2="1">
          <stop offset="0" stop-color="#1c2233"/>
          <stop offset="0.27" stop-color="#1c2233"/>
          <stop offset="0.3" stop-color="#e8ecf1"/>
          <stop offset="1" stop-color="#9aa1ad"/>
        </linearGradient>
      </defs>
      <rect x="43" y="0" width="34" height="824" fill="url(#bladeTone)"/>
    </svg>

    <h1 class="title">
      <span class="title-small">THE</span>
      <span class="title-main">LANTERN</span>
      <span class="title-main">COMPASS</span>
    </h1>

    <p class="subtitle">Quiet Methods for Growing Inner Steadiness and Calm Endurance</p>

    <p class="authors">Dorvelan Thaske &amp; Meloda Thaske</p>
  </main>
</body>
</html>
```